Business Cards - Brightpath Horizon

need to design unique business card for my mortgage business. I need to design credit card style business card for my business or any unique idea that you might have

Target Market(s)

Home Loan customers

Industry/Entity Type

Mortgage Brokerage

Contact Information for Business Card

please design credit card style or very unique style business card

Colors

Designer to choose colors to be used in the design.

Requirements
Must have
• Name
• position
• Phone number
• fax number
• email address
• website address
• social media address
• All above fields will be provided once design in finalised

```html
<!DOCTYPE html>
<html lang="en">
<head>
<meta charset="utf-8">
<title>Brightpath Horizon – Business Card</title>
<link href="https://fonts.googleapis.com/css2?family=Roboto:wght@400;500;700&display=swap" rel="stylesheet">
<style>
  :root {
    --stage: #2b2b2b;
    --card-white: #f2f2f2;
    --royal-blue: #0432c4;
    --sky-blue: #00aeef;
    --orange: #ff8c14;
    --white: #ffffff;
  }
  * { margin: 0; padding: 0; box-sizing: border-box; }
  html, body { width: 1200px; height: 960px; overflow: hidden; }
  body {
    background: var(--stage);
    font-family: "Roboto", Arial, sans-serif;
    position: relative;
  }
  .card {
    position: absolute;
    width: 600px;
    height: 342px;
    overflow: hidden;
  }
  .card-front { left: 314px; top: 113px; background: var(--card-white); }
  .card-back { left: 311px; top: 472px; background: var(--orange); }

  .front-brand {
    position: absolute;
    left: 31px; top: 74px;
    display: flex; align-items: center; gap: 8px;
    color: var(--royal-blue);
    font-weight: 700; font-size: 22px;
  }
  .brand-square { width: 14px; height: 14px; background: var(--orange); }

  .rooftop-art {
    position: absolute;
    left: 0; top: 78px;
    width: 600px; height: 144px;
    background: linear-gradient(180deg, rgba(242,242,242,0) 0%, rgba(0,174,239,0.35) 45%, rgba(4,50,196,0.85) 80%, var(--royal-blue) 100%);
  }
  .rooftop-accent {
    position: absolute;
    right: 0; top: 150px;
    width: 300px; height: 72px;
    background: linear-gradient(90deg, rgba(255,140,20,0) 0%, rgba(255,140,20,0.75) 100%);
  }

  .contact-band {
    position: absolute;
    left: 0; top: 222px;
    width: 600px; height: 120px;
    background: var(--royal-blue);
    color: var(--white);
  }
  .person { position: absolute; left: 31px; top: 16px; }
  .person-name { color: var(--sky-blue); font-weight: 700; font-size: 20px; line-height: 24px; }
  .person-role { font-weight: 500; font-size: 15px; line-height: 22px; }
  .person-address { font-size: 14.5px; line-height: 19px; margin-top: 8px; }

  .contact-list {
    position: absolute;
    right: 28px; top: 27px;
    list-style: none;
    font-size: 14.5px; line-height: 19.5px;
    text-align: right;
  }
  .contact-list li { display: flex; justify-content: flex-end; align-items: center; gap: 9px; }
  .contact-icon { width: 13px; height: 13px; fill: var(--sky-blue); }

  .back-brand {
    position: absolute;
    left: 0; top: 140px; width: 600px;
    display: flex; justify-content: center; align-items: center; gap: 14px;
    color: var(--white);
    font-weight: 700; font-size: 40px;
  }
  .back-brand .brand-square { width: 22px; height: 22px; background: var(--white); }

  .social-row {
    position: absolute;
    left: 70px; top: 290px; width: 460px; height: 30px;
    display: flex; align-items: center; justify-content: center; gap: 6px;
  }
  .social-rule { height: 1px; width: 160px; }
  .social-rule.left { background: linear-gradient(90deg, rgba(255,255,255,0), var(--white)); margin-right: 8px; }
  .social-rule.right { background: linear-gradient(90deg, var(--white), rgba(255,255,255,0)); margin-left: 8px; }
  .social-dot { width: 29px; height: 29px; border-radius: 50%; background: var(--white); }
</style>
</head>
<body>

<section class="card card-front">
  <div class="rooftop-art" role="img" aria-label="Illustration of overlapping house rooftops in blue and orange"></div>
  <div class="rooftop-accent" aria-hidden="true"></div>

  <div class="front-brand"><span class="brand-square"></span>Brightpath Horizon</div>

  <div class="contact-band">
    <div class="person">
      <p class="person-name">DANIEL MERCER</p>
      <p class="person-role">CEO/FOUNDER</p>
      <p class="person-address">4120 Willow Crest Dr<br>Juneau, Alaska 99801</p>
    </div>
    <ul class="contact-list">
      <li>555 218 4730
        <svg class="contact-icon" viewBox="0 0 16 16" aria-hidden="true"><path d="M3.5 1l2.5 3-1.5 1.8c.8 1.9 2.3 3.4 4.2 4.2L10.5 8.5l3 2.5-1.5 3C6.5 14 2 9.5 1 3.5z"/></svg>
      </li>
      <li>555 218 4731
        <svg class="contact-icon" viewBox="0 0 16 16" aria-hidden="true"><rect x="4" y="1" width="8" height="4"/><rect x="1" y="6" width="14" height="6" rx="1"/><rect x="4" y="10" width="8" height="5"/></svg>
      </li>
      <li>hello@brightpath.com
        <svg class="contact-icon" viewBox="0 0 16 16" aria-hidden="true"><path d="M1 3h14v1L8 9 1 4z"/><path d="M1 5.5l7 5 7-5V13H1z"/></svg>
      </li>
      <li>www.brightpath.com
        <svg class="contact-icon" viewBox="0 0 16 16" aria-hidden="true"><circle cx="8" cy="8" r="7"/></svg>
      </li>
    </ul>
  </div>
</section>

<section class="card card-back">
  <div class="back-brand"><span class="brand-square"></span>Brightpath Horizon</div>
  <div class="social-row">
    <span class="social-rule left"></span>
    <span class="social-dot"></span>
    <span class="social-dot"></span>
    <span class="social-dot"></span>
    <span class="social-dot"></span>
    <span class="social-rule right"></span>
  </div>
</section>

</body>
</html>
```